Marwick Law Letterhead

We need a new letterhead design for a Law Firm. The address for the law firm is 1475 Calloway Street, Suite 210, Houston, Texas 77041. Phone Number: 832-361-9027; Fax Number: 832-614-7359. The logo is uploaded to the project.

```html
<!DOCTYPE html>
<html lang="en">
<head>
<meta charset="utf-8">
<title>Marwick Law Letterhead</title>
<link rel="stylesheet" href="https://fonts.googleapis.com/css2?family=Montserrat:wght@400;500;600&display=swap">
<style>
  :root {
    --backdrop: #e9e9ea;
    --paper: #ffffff;
    --ink: #1c1c1c;
    --navy: #1f3a70;
    --red: #e5232a;
    --signature-tone: #d9d9d9;
  }
  * { box-sizing: border-box; margin: 0; padding: 0; }
  html, body {
    width: 1200px; height: 960px; overflow: hidden;
    background: var(--backdrop);
    font-family: "Montserrat", sans-serif;
    color: var(--ink);
  }
  .letterhead {
    position: absolute; left: 282px; top: 30px;
    width: 636px; height: 900px;
    background: var(--paper);
    box-shadow: 0 6px 18px rgba(0,0,0,0.12);
    overflow: hidden;
  }
  .brand {
    position: absolute; left: 44px; top: 58px;
    display: flex; align-items: center; gap: 10px;
  }
  .brand-mark {
    width: 30px; height: 30px; border-radius: 50%;
    background: var(--navy);
  }
  .brand-name {
    font-family: "Montserrat", sans-serif;
    font-weight: 600; font-size: 24px; letter-spacing: 0.5px;
    color: var(--navy);
  }
  .contact {
    position: absolute; right: 44px; top: 52px;
    font-size: 9.5px; line-height: 1.4;
  }
  .contact-line { display: flex; align-items: center; gap: 6px; }
  .contact-line svg { width: 8px; height: 8px; flex: none; }
  .contact-address { margin-bottom: 2px; }
  .recipient {
    position: absolute; left: 78px; top: 178px;
    font-size: 10px; line-height: 1.45;
  }
  .letter-body {
    position: absolute; left: 96px; top: 248px; width: 470px;
    font-size: 9.6px; line-height: 1.55; letter-spacing: 0.2px;
  }
  .letter-body p { margin-bottom: 14px; }
  .sign-off {
    position: absolute; left: 96px; top: 718px;
    font-size: 11px; font-weight: 500;
  }
  .signature {
    position: absolute; left: 110px; top: 738px;
    width: 90px; height: 34px; border-radius: 4px;
    background: var(--signature-tone);
  }
  .corner-bands {
    position: absolute; left: 0; bottom: 0;
    width: 636px; height: 70px;
  }
</style>
</head>
<body>
  <main class="letterhead">
    <header>
      <div class="brand">
        <span class="brand-mark"></span>
        <span class="brand-name">Marwick Law</span>
      </div>
      <address class="contact">
        <div class="contact-address">1475 Calloway Street,<br>Suite 210, Houston,<br>Texas 77041</div>
        <div class="contact-line">
          <svg viewBox="0 0 10 10"><path d="M2 1 L4 1 L5 3 L4 4 Q5 6 6 6 L7 5 L9 6 L9 8 Q8 9 7 9 Q1 8 1 3 Q1 2 2 1Z" fill="var(--red)"/></svg>
          <span>832-361-9027</span>
        </div>
        <div class="contact-line">
          <svg viewBox="0 0 10 10"><rect x="1" y="3" width="8" height="5" rx="1" fill="var(--red)"/><rect x="3" y="1" width="4" height="2" fill="var(--red)"/></svg>
          <span>832-614-7359</span>
        </div>
      </address>
    </header>

    <section class="recipient">
      <div>Mr/s</div>
      <div>First Name and Last Name</div>
      <div>Company Name</div>
      <div>Address</div>
    </section>

    <section class="letter-body">
      <p>Lorem ipsum dolor sit amet,consectetur adipiscing sed do eiusmod tempor incididunt laboreet dolore magna aliqua.Ut enim ad minim.veniam, quis nostrud exercitation ullamco laboris nisi ut aliquip exea commodo consequat.Lorem ipsum dolor sit amet,consectetur adipiscing sed do eiusmod tempor incididunt.labore et dolore magna aliqua. Ut enim</p>
      <p>Lorem ipsum dolor sit amet, consectetur adipiscing sed do eiusmod tempor incididunt labore et dolore magna aliqua. Ut enim ad minim veniam, quis nostrud exercitation ullamco laboris nisi ut aliquip exea commodo consequat.Duis aute irure dolor in reprehenderit in voluptate velit esse cillum irure dolor in reprehenderit in voluptate velit esse irure</p>
      <p>Lorem ipsum dolor sit amet, consectetur adipiscing sed do eiusmod tempor incididunt labore et dolore magna aliqua. consequat. Duis aute irure dolor in.reprehenderit in voluptate velit esse cillum dolore eu fugiat nulla pariatur. Excepteur sint occaecat cupidatat non proident, sunt in culpa qui officia deserunt mollit,</p>
      <p>Lorem ipsum dolor sit amet, consectetur adipiscing sed do eiusmod tempor incididunt labore et dolore magna aliqua. Ut enim Lorem ipsum dolor sit amet, consectetur adipiscing sed do eiusmod tempor incididunt labore et dolore magna aliqua. Ut enim Lorem ipsum aliqua.ipsum</p>
      <p>Lorem ipsum dolor sit amet, consectetur adipiscing sed do eiusmod tempor incididunt labore et dolore magna aliqua. Ut enim ad minim veniam, quis nostrud exercitation ullamco laboris nisi ut aliquip exea commodo consequat.Duis aute irure dolor in reprehenderit in voluptate velit esse cillum irure dolor in reprehenderit in voluptate velit esse irure</p>
      <p>Lorem ipsum dolor sit amet, consectetur adipiscing sed do eiusmod tempor incididunt labore et dolore magna aliqua. Ut enim ad minim veniam, quis nostrud exercitation ullamco laboris nisi ut aliquip exea commodo consequat.Duis aute irure dolor in reprehenderit in voluptate velit esse cillum irure dolor in reprehenderit in voluptate velit esse irure</p>
    </section>

    <div class="sign-off">Regards</div>
    <div class="signature" role="img" aria-label="Handwritten signature"></div>

    <svg class="corner-bands" viewBox="0 0 636 70" preserveAspectRatio="none" aria-hidden="true">
      <polygon points="0,62 430,40 436,40 430,70 0,70" fill="var(--red)"/>
      <polygon points="436,26 636,0 636,70 432,70" fill="var(--navy)"/>
    </svg>
  </main>
</body>
</html>
```